Business Card Design Project

This is to go hand in hand with our stationery project.
Target Market(s)
Business Professionals in the Finance, HR and C-Level management arena. They are global companies that run enterprise technology solutions/products.
Mostly Male, mid 30's to 60's.
Industry/Entity Type
Business
Font styles to use
Other font styles liked:
- Calibri
Colors
9bcb3c
000000
1b1b1b
c4c4c4
ffffff
Requirements
Must have
- Logo
Name, title, contact details, address on the front of the card.
ABN and web address need to be on the card, along with our tag line
See | Share | Do
We also require rounded corners and for the card to be landscape please.
Our green is
C98 M0 Y93 K0
Modern, contemporary and must have white space for people to write on.
Nice to have
- Consistent elements with the stationery design.
Should not have
- No 90's waves - We want the feeling of movement but no wavey lines.

```html
<!DOCTYPE html>
<html lang="en">
<head>
<meta charset="utf-8">
<title>Business Card – Marissa Delcourtova</title>
<link rel="stylesheet" href="https://fonts.googleapis.com/css2?family=Carlito:wght@400;700&display=swap">
<style>
  :root {
    --brand-green: #9bcb3c;
    --ink: #333333;
    --paper: #ffffff;
  }
  html, body {
    margin: 0;
    padding: 0;
    width: 1200px;
    height: 720px;
    overflow: hidden;
    background: var(--paper);
  }
  .card {
    position: relative;
    width: 1200px;
    height: 720px;
    background: var(--paper);
    font-family: "Carlito", Calibri, sans-serif;
    font-weight: 700;
    color: var(--ink);
  }
  .accent-bar {
    position: absolute;
    left: 190px;
    width: 66px;
    background: var(--brand-green);
  }
  .accent-bar--top {
    top: 78px;
    height: 192px;
    border-radius: 0 0 33px 33px;
  }
  .accent-bar--bottom {
    top: 440px;
    height: 192px;
    border-radius: 33px 33px 0 0;
  }
  .identity {
    position: absolute;
    left: 282px;
    right: 270px;
    top: 140px;
    text-align: right;
  }
  .identity__name {
    margin: 0;
    font-size: 58px;
    line-height: 1;
    letter-spacing: 0.2px;
  }
  .identity__title {
    margin: 2px 0 0;
    font-size: 35px;
    line-height: 1;
  }
  .contact {
    position: absolute;
    left: 199px;
    top: 284px;
    margin: 0;
    padding: 0;
    list-style: none;
  }
  .contact__line {
    font-size: 42px;
    line-height: 50px;
    letter-spacing: 0.5px;
  }
  .contact__label {
    color: var(--brand-green);
  }
  .contact__web {
    font-size: 35px;
    line-height: 44px;
    color: var(--brand-green);
    letter-spacing: 0.6px;
  }
  .address {
    position: absolute;
    right: 590px;
    top: 474px;
    text-align: right;
    font-style: normal;
    font-size: 25px;
    line-height: 36px;
    color: var(--brand-green);
  }
  .address__abn {
    margin-top: 4px;
    font-size: 27px;
  }
  .address__abn-number {
    color: var(--ink);
  }
  .motion-graphic {
    position: absolute;
    left: 760px;
    top: 405px;
    width: 346px;
    height: 228px;
    border-radius: 40px 40px 40px 40px;
    background: linear-gradient(200deg, rgba(155, 203, 60, 0.15) 0%, rgba(155, 203, 60, 0.55) 55%, rgba(155, 203, 60, 0.9) 100%);
  }
</style>
</head>
<body>
  <div class="card">
    <div class="accent-bar accent-bar--top"></div>
    <div class="accent-bar accent-bar--bottom"></div>

    <header class="identity">
      <h1 class="identity__name">Marissa Delcourtova</h1>
      <p class="identity__title">Job Title</p>
    </header>

    <ul class="contact">
      <li class="contact__line"><span class="contact__label">T:</span> + 61 2 9000 4821</li>
      <li class="contact__line"><span class="contact__label">F:</span> +61 2 9000 4822</li>
      <li class="contact__web">www.novexpartners.com</li>
    </ul>

    <address class="address">
      <div>Level 4, 210 Harbour Road,</div>
      <div>Eastwood Bay NSW 2999</div>
      <div class="address__abn">ABN: <span class="address__abn-number">12 345 678 901</span></div>
    </address>

    <div class="motion-graphic" role="img" aria-label="Decorative field of green dots growing in size toward the lower left, suggesting movement"></div>
  </div>
</body>
</html>
```